Market Research firm needs updated business cards with new logo

We need the logo to be included somewhere on the card (attached). We would also like the phrases "Independent, Objective, Comprehensive" and "Research You Can Trust" somewhere on the card. Front or back. Our colors are hex codes 6075a7, e48d25 and 5a5b5b. Though you are certainly not limited to those shades, whatever you produce should coordinate with them. I have also attached our favicon. Feel free to use it in your design, but please do not use it to replace the full logo.

Contact Information for Business Card

see project description

Font styles to use
Other font styles liked:
• Open Sans

Requirements
Must have
• the logo
• We use Open Sans font

```html
<!DOCTYPE html>
<html lang="en">
<head>
<meta charset="utf-8">
<title>Halvern Research – Business Card</title>
<link rel="stylesheet" href="https://fonts.googleapis.com/css2?family=Open+Sans:wght@400;600;700&display=swap">
<style>
  :root {
    --stage: #d9d9d9;
    --card: #5a5b5b;
    --orange: #e48d25;
    --blue: #6075a7;
  }
  * { margin: 0; padding: 0; box-sizing: border-box; }
  html, body {
    width: 1200px; height: 1200px; overflow: hidden;
    background: var(--stage);
    font-family: "Open Sans", Arial, sans-serif;
  }
  .canvas { position: relative; width: 1200px; height: 1200px; }
  .card {
    position: absolute; left: 100px; width: 1000px; height: 520px;
    background: var(--card); overflow: hidden;
  }
  .card-front { top: 40px; }
  .card-back { top: 600px; }

  .brand {
    position: absolute; display: flex; align-items: center;
    color: var(--orange); font-weight: 600; white-space: nowrap; line-height: 1;
  }
  .brand-dot { border-radius: 50%; background: var(--orange); flex: none; }
  .card-front .brand { left: 70px; top: 70px; font-size: 50px; gap: 16px; }
  .card-front .brand-dot { width: 26px; height: 26px; }
  .card-back .brand {
    left: 50%; top: 50%; transform: translate(-50%, -50%);
    font-size: 88px; gap: 26px;
  }
  .card-back .brand-dot { width: 44px; height: 44px; }

  .person {
    position: absolute; right: 60px; top: 190px;
    color: var(--orange); line-height: 1.1;
  }
  .person-name { font-size: 46px; font-weight: 700; letter-spacing: 1px; }
  .person-role { font-size: 30px; font-weight: 400; margin-top: 2px; margin-left: 4px; }

  .contact-band {
    position: absolute; left: 0; top: 300px; width: 100%; height: 110px;
    display: flex; font-size: 26px;
  }
  .contact-band span { display: flex; align-items: center; justify-content: center; }
  .contact-email { width: 330px; background: var(--orange); color: var(--blue); }
  .contact-phone { width: 360px; background: var(--blue); color: var(--orange); }
  .contact-web { flex: 1; background: var(--orange); color: var(--blue); }

  .taglines {
    position: absolute; left: 40px; right: 50px; top: 438px;
    display: flex; justify-content: space-between;
    color: var(--orange); font-size: 30px;
  }
</style>
</head>
<body>
<main class="canvas">
  <section class="card card-front">
    <div class="brand"><span class="brand-dot"></span>Halvern Research</div>
    <div class="person">
      <p class="person-name">JOHN SMITH</p>
      <p class="person-role">Owner</p>
    </div>
    <div class="contact-band">
      <span class="contact-email">hello@halvernmail.com</span>
      <span class="contact-phone">555 0192 4817</span>
      <span class="contact-web">www.yourwebsite.com</span>
    </div>
    <div class="taglines">
      <span>Independent</span>
      <span>Comprehensive</span>
      <span>Research You Can Trust</span>
    </div>
  </section>

  <section class="card card-back">
    <div class="brand"><span class="brand-dot"></span>Halvern Research</div>
  </section>
</main>
</body>
</html>
```